Poster Required for Cafe to promote Catering

I would like a Poster made to advertise that our business does catering.
On the poster we would like it to say:

Did you know that Wren Hollow does Catering?
We offer Breakfast, Lunch, Morning and Afternoon Tea Options
Come instore to enquire

At the bottom of the flyer, can you please put the contact details:
Phone 0462 917 504
Email tam@wrenhollowcanteen.com

Poster Size A3

I have attached our logo and menu's so you can get a feel for what we like.

Target Market(s)

Hospital Staff: Doctors, Nurses, Admin

Industry/Entity Type

Hospitality

Requirements
Nice to have
• Some pictures of catering. Eg. Gourmet Sandwiches, Sliders
• You could check our instagram page for ideas on what we do..
• @wrnhollow_qld

```html
<!DOCTYPE html>
<html lang="en">
<head>
<meta charset="utf-8">
<title>Wren Hollow Catering Poster</title>
<link rel="stylesheet" href="https://fonts.googleapis.com/css2?family=Old+Standard+TT&family=Arimo:wght@400;700&family=Open+Sans:wght@700&display=swap">
<style>
  :root {
    --page-bg: #e9e9e7;
    --poster-yellow: #f8f1a6;
    --poster-yellow-light: #fbf6c4;
    --ink: #2e2424;
    --ribbon-text: #f8f1a6;
  }
  * { margin: 0; padding: 0; box-sizing: border-box; }
  html, body {
    width: 1200px;
    height: 1148px;
    overflow: hidden;
    background: var(--page-bg);
  }
  .poster {
    position: absolute;
    left: 218px;
    top: 34px;
    width: 764px;
    height: 1080px;
    background: linear-gradient(160deg, var(--poster-yellow-light), var(--poster-yellow));
    color: var(--ink);
    text-align: center;
  }
  .poster__frame {
    position: absolute;
    left: 96px;
    right: 96px;
    top: 78px;
    height: 706px;
    border: 3px solid var(--ink);
  }
  .headline {
    position: absolute;
    left: 0;
    right: 0;
    font-family: "Old Standard TT", serif;
    font-weight: 400;
    font-size: 44px;
    letter-spacing: 0.5px;
  }
  .headline--top { top: 150px; }
  .headline--bottom { top: 490px; }
  .brand {
    position: absolute;
    left: 0;
    right: 0;
    top: 300px;
    display: flex;
    justify-content: center;
    align-items: center;
    gap: 18px;
  }
  .brand__dot {
    width: 40px;
    height: 40px;
    border-radius: 50%;
    background: var(--ink);
  }
  .brand__name {
    font-family: "Old Standard TT", serif;
    font-size: 40px;
    letter-spacing: 2px;
    color: var(--ink);
  }
  .offer {
    position: absolute;
    left: 0;
    right: 0;
    top: 700px;
    font-family: "Arimo", sans-serif;
    font-size: 14px;
    line-height: 22px;
    text-transform: uppercase;
  }
  .ribbon {
    position: absolute;
    left: 190px;
    top: 764px;
    width: 384px;
    height: 44px;
    background: var(--ink);
    display: flex;
    align-items: center;
    justify-content: center;
  }
  .ribbon__text {
    font-family: "Open Sans", sans-serif;
    font-weight: 700;
    font-size: 19px;
    letter-spacing: 1px;
    color: var(--ribbon-text);
    text-transform: uppercase;
  }
  .contact {
    position: absolute;
    left: 0;
    right: 0;
    font-family: "Arimo", sans-serif;
    color: var(--ink);
  }
  .contact--phone { top: 826px; font-size: 22px; font-weight: 700; }
  .contact--email { top: 870px; font-size: 22px; letter-spacing: 2.6px; }
</style>
</head>
<body>
  <main class="poster">
    <div class="poster__frame"></div>
    <h1 class="headline headline--top">DID YOU KNOW</h1>
    <div class="brand">
      <span class="brand__dot"></span>
      <span class="brand__name">WREN HOLLOW</span>
    </div>
    <h2 class="headline headline--bottom">DOES CATERING?</h2>
    <p class="offer">We offer breakfast,<br>lunch and morning and afternoon tea options</p>
    <div class="ribbon" role="img" aria-label="Ribbon banner with call to action">
      <span class="ribbon__text">Come in store to enquire</span>
    </div>
    <p class="contact contact--phone">Phone 0462 917 504</p>
    <p class="contact contact--email">email:tam@wrenhollowcanteen.com</p>
  </main>
</body>
</html>
```